The most modern business card ever !!!

Our company call “Vendalo”. Vendalo is a technology company specialized in cruises solutions. Out main product is a platform to reserve cruises. This is a revolutionary platform that make easier to travel agencies and final users to reserve cruises across dozen companies like tibba, wernu, hpv, dgb, etc..We are a “start up”, with a young team of developers and we want to transmit it.. For it, we want something different, a modern business card that represent cruises and technology.. When someone receive this card, this person should say: wowww this is different… this is modern… this is a cruise related company..
- diferent, modern
- traditions business card

```html
<!DOCTYPE html>
<html lang="en">
<head>
<meta charset="utf-8">
<title>Vendalo — Business Card</title>
<link href="https://fonts.googleapis.com/css2?family=Lato:wght@400;700&display=swap" rel="stylesheet">
<style>
  :root {
    --backdrop: #bcbcbc;
    --card-dark: #2b2b2d;
    --brand-emboss: #242426;
    --card-light: #f4f5f4;
    --ink: #111111;
    --ink-soft: #2a2a2a;
    --accent: #2ea3dc;
  }
  * { box-sizing: border-box; margin: 0; padding: 0; }
  html, body {
    width: 1200px; height: 1200px; overflow: hidden;
    background: var(--backdrop);
    font-family: "Lato", Arial, sans-serif;
  }
  .card {
    position: absolute;
    left: 250px;
    width: 708px;
    height: 403px;
    border-radius: 24px;
  }
  .card--front {
    top: 144px;
    background: var(--card-dark);
    display: flex; align-items: center; justify-content: center;
  }
  .card--front .brand-name {
    font-weight: 700;
    font-size: 104px;
    letter-spacing: 2px;
    color: var(--brand-emboss);
    margin-top: -4px;
  }
  .card--back {
    top: 582px;
    background: var(--card-light);
  }
  .card--back .brand-name {
    position: absolute;
    right: 54px; top: 34px;
    font-weight: 700;
    font-size: 68px;
    letter-spacing: 1px;
    color: var(--ink);
  }
  .person { position: absolute; left: 50px; top: 214px; }
  .person__name { font-weight: 700; font-size: 22px; color: var(--ink); }
  .person__role { font-size: 17px; color: var(--accent); margin-top: 2px; }
  .contact-list {
    position: absolute; left: 50px; top: 300px;
    list-style: none;
  }
  .contact-list li {
    display: flex; align-items: center; gap: 9px;
    font-size: 17px; line-height: 22.5px; color: var(--ink-soft);
  }
  .contact-list svg { width: 12px; height: 12px; fill: var(--accent); flex: none; }
  .contact-list .highlight { color: var(--accent); }
  .address {
    position: absolute; right: 54px; top: 322px;
    text-align: right;
    font-size: 17px; line-height: 23px; color: var(--ink-soft);
    font-style: normal;
  }
</style>
</head>
<body>
  <section class="card card--front" aria-label="Card front">
    <div class="brand-name">Vendalo</div>
  </section>

  <section class="card card--back" aria-label="Card back">
    <div class="brand-name">Vendalo</div>

    <div class="person">
      <p class="person__name">Dara Whitcombe</p>
      <p class="person__role">Director</p>
    </div>

    <ul class="contact-list">
      <li>
        <svg viewBox="0 0 12 12" aria-hidden="true"><path d="M2.4 0.5 L4.3 2.6 L3.3 4.1 C3.9 5.6 5.3 7.3 7 8.2 L8.4 7.2 L10.8 9 L9.6 11.2 C5.2 11.5 0.6 6.3 0.6 1.6 Z"/></svg>
        +244 555 019
      </li>
      <li>
        <svg viewBox="0 0 12 12" aria-hidden="true"><path d="M0.5 2.5 H11.5 V10 H0.5 Z M1.2 3 L6 6.8 L10.8 3 Z" fill-rule="evenodd"/></svg>
        info@vendalo.com
      </li>
      <li>
        <svg viewBox="0 0 12 12" aria-hidden="true"><circle cx="6" cy="6" r="5.3" fill="none" stroke="#2ea3dc" stroke-width="0.9"/><ellipse cx="6" cy="6" rx="2.3" ry="5.3" fill="none" stroke="#2ea3dc" stroke-width="0.9"/><path d="M0.7 4.3 H11.3 M0.7 7.7 H11.3" stroke="#2ea3dc" stroke-width="0.9"/></svg>
        <span>www.<span class="highlight">vendalo</span>.com</span>
      </li>
    </ul>

    <address class="address">
      47/3 Harbour Lane<br>
      Marlowe,TS.600512-XYZ
    </address>
  </section>
</body>
</html>
```